i need a business card design for my family investment company "quorin investments" based in dubai. its a diverse investment firm focusing on education, hospitality and automotive. the design has to be modern and try to incorporate the logo "E" in the design. details on card as follow

Yusuf K Bin Tarrah
Managing Director
yusuf@quorin-mail.ae
www.quorin-mail.ae

Harbor district,palwick tower, office 1847, dubai
tel. 04 3850927
mobile.050 9184203

card used for networking events and investor meetings

Hospitality

```html
<!DOCTYPE html>
<html lang="en">
<head>
<meta charset="utf-8">
<title>Quorin Investments – Business Card</title>
<link href="https://fonts.googleapis.com/css2?family=Quicksand:wght@400;500;700&display=swap" rel="stylesheet">
<style>
  :root {
    --backdrop: #d4d4d4;
    --card-blue: #3a71b1;
    --ink-white: #ffffff;
    --ink-soft: #dce7f5;
    --rule: rgba(255,255,255,0.45);
  }
  * { box-sizing: border-box; margin: 0; padding: 0; }
  html, body {
    width: 1200px; height: 1000px; overflow: hidden;
    background: var(--backdrop);
    font-family: "Quicksand", "Century Gothic", sans-serif;
  }
  .canvas {
    position: relative; width: 1200px; height: 1000px;
  }
  .card {
    position: absolute; left: 250px;
    width: 700px; height: 400px;
    background: var(--card-blue);
    color: var(--ink-white);
    box-shadow: 0 6px 18px rgba(0,0,0,0.18);
  }
  .card--front { top: 60px; }
  .card--back { top: 540px; }

  .brand-name {
    position: absolute; left: 0; right: 0;
    text-align: center;
    font-weight: 500;
    text-transform: uppercase;
    color: var(--ink-white);
    white-space: nowrap;
  }
  .card--front .brand-name {
    top: 46px; font-size: 30px; letter-spacing: 5px;
  }
  .card--back .brand-name {
    top: 168px; font-size: 44px; letter-spacing: 7px;
  }

  .holder {
    position: absolute; left: 40px; top: 214px;
  }
  .holder__name {
    font-weight: 700; font-size: 22px; letter-spacing: 0.3px;
  }
  .holder__title {
    font-weight: 400; font-size: 16px; color: var(--ink-soft); margin-top: 4px;
  }

  .contact {
    position: absolute; left: 410px; top: 180px;
    padding-left: 16px;
    border-left: 1px solid var(--rule);
    font-size: 16px; line-height: 24px;
    color: var(--ink-soft);
    white-space: nowrap;
  }
  .contact__address { margin-bottom: 2px; }
  .contact__row { display: flex; align-items: center; gap: 6px; }
  .contact__icon { width: 14px; height: 14px; flex: none; }
</style>
</head>
<body>
<main class="canvas">

  <section class="card card--front" aria-label="Business card front">
    <div class="brand-name">Quorin Investments</div>

    <div class="holder">
      <div class="holder__name">Yusuf K Bin Tarrah</div>
      <div class="holder__title">Managing Director</div>
    </div>

    <div class="contact">
      <div class="contact__address">Harbor district, palwick tower,<br>office 1847, dubai</div>
      <div class="contact__row">
        <svg class="contact__icon" viewBox="0 0 16 16" aria-hidden="true"><path d="M4 1.5l2.5 3-1.5 1.6c.8 1.9 2.2 3.3 4 4.2l1.6-1.5 3 2.4-1.4 2.8C7 13.5 2.5 9 2 3z" fill="#fff"/></svg>
        <span>: 04 3850927</span>
      </div>
      <div class="contact__row">
        <svg class="contact__icon" viewBox="0 0 16 16" aria-hidden="true"><rect x="4" y="1" width="8" height="14" rx="1.5" fill="#fff"/><rect x="5.5" y="3" width="5" height="5" fill="#3a71b1"/></svg>
        <span>: 050 9184203</span>
      </div>
      <div class="contact__row">
        <svg class="contact__icon" viewBox="0 0 16 16" aria-hidden="true"><rect x="1" y="3.5" width="14" height="9" fill="#fff"/><path d="M1 3.5l7 5 7-5" fill="none" stroke="#3a71b1" stroke-width="1.2"/></svg>
        <span>: yusuf@quorin-mail.ae</span>
      </div>
      <div class="contact__row">
        <svg class="contact__icon" viewBox="0 0 16 16" aria-hidden="true"><circle cx="8" cy="8" r="6.5" fill="none" stroke="#fff" stroke-width="1.2"/><ellipse cx="8" cy="8" rx="3" ry="6.5" fill="none" stroke="#fff" stroke-width="1"/><line x1="1.5" y1="8" x2="14.5" y2="8" stroke="#fff" stroke-width="1"/></svg>
        <span>: www.quorin-mail.ae</span>
      </div>
    </div>
  </section>

  <section class="card card--back" aria-label="Business card back">
    <div class="brand-name">Quorin Investments</div>
  </section>

</main>
</body>
</html>
```